Business card design for holistic health care clinic

We need a double-sided business card design for our holistic health care clinic that integrates our logo design and also its color scheme. My business is called Valmira. It is an integrative medicine clinic. You have already done the logo for me. Please ensure an elegant and upscale design that is not cluttered, but still has all the necessary information (please see below for details).

Target Market(s)

Wellness, fitness, rehabilitation for educated, well-traveled open-minded clients who are focused on natural, organic, balanced and preventive healthcare and lifestyle.

Industry/Entity Type

Medical

Contact Information for Business Card

Modern, clean.

Number of Pages Required

1 page

Font styles to use
Serif
Sans Serif

Colors

Designer to choose colors to be used in the design.

Requirements
Must have
• Logo on one side, all other information on the other side.
• Other information should include:
• Tobias Wrenfeld - DOE, CPT, LMT
• 4100 East Marrow Drive
• Austin, TX 78119
• 512 555 0148
• 818 555 0192
• info@ValmiraHealth.example
• t.wrenfeld@ValmiraHealth.example
Nice to have
• Darker background on front - but not totally black - shaded/dark gray.

```html
<!DOCTYPE html>
<html lang="en">
<head>
<meta charset="utf-8">
<title>Valmira — Business Card</title>
<link rel="stylesheet" href="https://fonts.googleapis.com/css2?family=Roboto:wght@400;700&family=Roboto+Condensed:wght@700&family=Nunito:wght@800&display=swap">
<style>
  :root {
    --page: #ebe8e3;
    --brand-blue: #0a90cd;
    --charcoal: #2a2a2a;
    --card-white: #f4f4f4;
    --ink: #ffffff;
    --tagline-ink: #444444;
  }
  * { margin: 0; padding: 0; box-sizing: border-box; }
  html, body {
    width: 1200px; height: 960px; overflow: hidden;
    background: var(--page);
  }
  .canvas { position: relative; width: 1200px; height: 960px; }

  .card {
    position: absolute; width: 600px; height: 343px; overflow: hidden;
    box-shadow: 0 2px 4px rgba(0,0,0,0.25);
  }
  .card-front { left: 314px; top: 113px; background: var(--charcoal); }
  .card-back  { left: 311px; top: 471px; background: var(--card-white); }

  .front-shape { position: absolute; inset: 0; width: 600px; height: 343px; }

  .contact {
    position: absolute; left: 40px; top: 108px;
    color: var(--ink);
    font-family: "Roboto", Arial, sans-serif;
    font-size: 14.5px; line-height: 19px;
  }
  .contact-name {
    font-family: "Roboto Condensed", "Arial Narrow", sans-serif;
    font-weight: 700; font-size: 21px; line-height: 24px;
    text-transform: uppercase; letter-spacing: 0.2px;
  }
  .contact-credentials {
    font-family: "Roboto Condensed", "Arial Narrow", sans-serif;
    font-weight: 700; font-size: 12px; line-height: 14px;
    margin-bottom: 20px;
  }
  .contact-label { font-weight: 700; }
  .divider {
    border: 0; border-top: 1px dotted rgba(255,255,255,0.85);
    margin: 6px 0 10px;
  }
  .divider-short { width: 133px; }
  .divider-long { width: 170px; }

  .brand-name {
    position: absolute;
    font-family: "Nunito", Arial, sans-serif;
    font-weight: 800; color: var(--brand-blue);
    letter-spacing: 1px; line-height: 1;
  }
  .card-front .brand-name { left: 316px; width: 240px; top: 88px; font-size: 52px; text-align: center; }
  .card-back .brand-name { left: 0; width: 600px; top: 150px; font-size: 60px; text-align: center; }

  .tagline {
    position: absolute; left: 0; width: 600px; top: 292px;
    text-align: center;
    font-family: "Roboto", Arial, sans-serif;
    font-size: 14px; color: var(--tagline-ink);
  }
</style>
</head>
<body>
<main class="canvas">

  <section class="card card-front" aria-label="Card front">
    <svg class="front-shape" viewBox="0 0 600 343" aria-hidden="true">
      <polygon points="0,0 140,0 370,343 0,343" fill="var(--brand-blue)"/>
      <line x1="150" y1="14" x2="371" y2="343" stroke="#ffffff" stroke-width="3"/>
    </svg>

    <div class="contact">
      <p class="contact-name">Tobias Wrenfeld</p>
      <p class="contact-credentials">DOE, CPT, LMT</p>
      <p><span class="contact-label">P:</span> 512 555 0148</p>
      <p><span class="contact-label">C:</span> 818 555 0192</p>
      <hr class="divider divider-short">
      <p>4100 East Marrow Drive</p>
      <p>Austin, TX 78119</p>
      <hr class="divider divider-long">
      <p>t.wrenfeld@ValmiraHealth.example</p>
      <p>www.ValmiraHealth.example</p>
    </div>

    <p class="brand-name">VALMIRA</p>
  </section>

  <section class="card card-back" aria-label="Card back">
    <p class="brand-name">VALMIRA</p>
    <p class="tagline">wellness made personal — your pace, your balance</p>
  </section>

</main>
</body>
</html>
```